Business Card Design for Marketing Firm

Looking for business card design for higher end marketing firm. Clean but impressionable/trendy. We are a marketing firm that represents manufacturers in the foodservice equipment and supply industry. Our customers are end users such has hotels, restaurants, country clubs, convention centers and casinos as well as distributors of restaurants supplies and equipment, and manufacturers of foodservice equipment and supplies.
Target Market(s)
Hotels, Restaurants, Supply & Equipment Distributors, Foodservice Manufacturers
Industry/Entity Type
Foodservice/Hospitality
Contact Information for Business Card
Name, Title, Contact Number, Email, Website, Social Media, Address
Requirements
Must have
- Clean & Simple but Serious and Impressionable

```html
<!DOCTYPE html>
<html lang="en">
<head>
<meta charset="utf-8">
<title>Meridian Service Reps – Business Card</title>
<link href="https://fonts.googleapis.com/css2?family=Open+Sans:wght@400;600;700&display=swap" rel="stylesheet">
<style>
  :root {
    --navy: #262b78;
    --white: #ffffff;
    --ink: #2a2a2a;
    --backdrop: #3a3533;
  }
  * { margin: 0; padding: 0; box-sizing: border-box; }
  html, body {
    width: 1200px; height: 786px; overflow: hidden;
    background: var(--backdrop);
    font-family: "Open Sans", Arial, sans-serif;
  }
  .canvas {
    position: relative; width: 1200px; height: 786px;
    display: flex; align-items: center; justify-content: center; gap: 40px;
  }
  .card {
    position: relative; width: 540px; height: 309px;
    box-shadow: 0 10px 30px rgba(0,0,0,.45);
  }
  .card--front { background: var(--white); color: var(--navy); }
  .card--back {
    background: var(--navy); color: var(--white);
    display: flex; align-items: center; justify-content: center;
  }

  .brand {
    display: flex; align-items: center; gap: 12px;
    font-weight: 600; letter-spacing: .08em; text-transform: uppercase;
  }
  .brand__dot { border-radius: 50%; flex: none; }
  .brand__name { line-height: 1.2; }

  .card--front .brand {
    position: absolute; left: 34px; top: 0; bottom: 0; width: 200px;
    font-size: 17px; color: var(--navy);
  }
  .card--front .brand__dot { width: 14px; height: 14px; background: var(--navy); }

  .card--back .brand { font-size: 28px; }
  .card--back .brand__dot { width: 22px; height: 22px; background: var(--white); }

  .divider {
    position: absolute; left: 262px; top: 46px; width: 2px; height: 190px;
    background: var(--navy);
  }

  .details { position: absolute; left: 286px; top: 40px; right: 20px; }
  .person__name { font-size: 17px; font-weight: 700; text-transform: uppercase; color: var(--navy); }
  .person__title { font-size: 11px; color: var(--ink); margin-bottom: 14px; }

  .contact { list-style: none; font-size: 11.5px; color: var(--ink); }
  .contact li { display: flex; align-items: center; gap: 8px; margin-bottom: 5px; }
  .contact svg { width: 12px; height: 12px; fill: var(--navy); flex: none; }

  .address { font-size: 11.5px; color: var(--ink); margin-top: 14px; line-height: 1.45; }

  .follow {
    position: absolute; left: 286px; bottom: 28px;
    display: flex; align-items: center; gap: 14px;
  }
  .follow__label { font-size: 19px; font-weight: 600; color: var(--navy); }
  .follow__icons { display: flex; gap: 4px; }
  .follow__icons span { width: 16px; height: 16px; border-radius: 50%; background: var(--navy); }
</style>
</head>
<body>
<main class="canvas">
  <section class="card card--front">
    <div class="brand">
      <span class="brand__dot"></span>
      <span class="brand__name">Meridian Service Reps</span>
    </div>
    <div class="divider"></div>
    <div class="details">
      <p class="person__name">Daniel Reed</p>
      <p class="person__title">Managing Director</p>
      <ul class="contact">
        <li><svg viewBox="0 0 24 24"><path d="M6.6 10.8a15.1 15.1 0 0 0 6.6 6.6l2.2-2.2a1 1 0 0 1 1-.25 11.4 11.4 0 0 0 3.6.6 1 1 0 0 1 1 1V20a1 1 0 0 1-1 1A17 17 0 0 1 3 4a1 1 0 0 1 1-1h3.5a1 1 0 0 1 1 1 11.4 11.4 0 0 0 .6 3.6 1 1 0 0 1-.25 1z"/></svg>123 456 789</li>
        <li><svg viewBox="0 0 24 24"><path d="M2 5h20v14H2zm2 2v.5l8 5 8-5V7l-8 5z"/></svg>info@yourgmail.com</li>
        <li><svg viewBox="0 0 24 24"><path d="M12 2a10 10 0 1 0 0 20 10 10 0 0 0 0-20zm0 2c1 0 2.4 2.3 2.8 6H9.2C9.6 6.3 11 4 12 4zM4.1 13h3.1c.1 2 .5 3.8 1.1 5.2A8 8 0 0 1 4.1 13zm0-2a8 8 0 0 1 4.2-6.2C7.7 6.2 7.3 8.9 7.2 11zm5.1 2h5.6c-.4 3.7-1.8 6-2.8 6s-2.4-2.3-2.8-6zm6.5 5.2c.6-1.4 1-3.2 1.1-5.2h3.1a8 8 0 0 1-4.2 5.2zM16.8 11c-.1-2.1-.5-4.8-1.1-6.2A8 8 0 0 1 19.9 11z"/></svg>www.yourwebsite.com</li>
      </ul>
      <p class="address">Your address, City<br>State, Zip 1234</p>
    </div>
    <div class="follow">
      <span class="follow__label">Follow Us</span>
      <div class="follow__icons" aria-label="Social media links">
        <span></span><span></span><span></span><span></span><span></span><span></span>
      </div>
    </div>
  </section>

  <section class="card card--back">
    <div class="brand">
      <span class="brand__dot"></span>
      <span class="brand__name">Meridian Service Reps</span>
    </div>
  </section>
</main>
</body>
</html>
```